Business Card Design Project

We are an incubator company that helps young entrepreneur to launch new ideas into the market. We will be targeting investors or likewise; Angels, young entrepreneurs and technopreneurs.

Our logo is being tasked by pixelhive to design, therefore there is no logo for now.
You can us Lanternfield Pte Ltd as the logo for the time being.

Please let us have some versions of modern and yet professional designs; for words, you can indicate e.g (address), (Title)

thanks

Target Market(s)

young entrepreneurs
angels, investors

Industry/Entity Type

Business

Colors
3176b5
ffffff

Requirements
Must have
• able to project out our name; Lanternfield
Should not have
• Nothing childish or cartoon

```html
<!DOCTYPE html>
<html lang="en">
<head>
<meta charset="utf-8">
<title>Lanternfield Business Card</title>
<link rel="stylesheet" href="https://fonts.googleapis.com/css2?family=Montserrat:wght@600&family=Open+Sans:wght@400;600&display=swap">
<style>
  :root {
    --backdrop: #6e6d68;
    --card-white: #ffffff;
    --slate: #4a5168;
    --slate-deep: #323b4f;
    --accent-blue: #0a93b8;
    --contact-panel: #414860;
    --contact-text: #b8bdcb;
  }
  html, body {
    margin: 0;
    width: 1200px;
    height: 900px;
    overflow: hidden;
    background: var(--backdrop);
  }
  .stage {
    width: 1200px;
    height: 900px;
    display: flex;
    align-items: center;
    justify-content: center;
  }
  .business-card {
    width: 980px;
    height: 560px;
    background: var(--card-white);
    box-shadow: 0 10px 30px rgba(0,0,0,0.25);
  }
  .business-card svg { display: block; }
  .brand-name {
    font-family: "Montserrat", sans-serif;
    font-weight: 600;
  }
  .person-name,
  .person-title,
  .contact-line {
    font-family: "Open Sans", sans-serif;
    font-weight: 400;
  }
</style>
</head>
<body>
<main class="stage">
  <section class="business-card" aria-label="Lanternfield business card">
    <svg width="980" height="560" viewBox="0 0 980 560">
      <defs>
        <clipPath id="shape-field"><rect width="895" height="560"/></clipPath>
      </defs>
      <rect class="card-base" width="980" height="560" fill="var(--card-white)"/>

      <g class="card-shapes" clip-path="url(#shape-field)">
        <!-- top-left emblem disc -->
        <circle class="emblem-rim" cx="52" cy="62" r="226" fill="var(--accent-blue)"/>
        <circle class="emblem-disc" cx="40" cy="40" r="222" fill="var(--slate-deep)"/>

        <!-- lower-right accent arc -->
        <circle class="corner-arc" cx="940" cy="640" r="300" fill="var(--accent-blue)"/>

        <!-- bottom-left hill -->
        <ellipse class="base-hill" cx="330" cy="650" rx="420" ry="225" fill="var(--slate)"/>

        <!-- name disc with rim -->
        <circle class="name-disc-rim" cx="628" cy="490" r="268" fill="var(--accent-blue)"/>
        <circle class="name-disc" cx="620" cy="500" r="260" fill="var(--slate)"/>
      </g>

      <!-- brand placeholder in emblem -->
      <rect class="brand-square" x="30" y="62" width="22" height="22" fill="var(--card-white)"/>
      <text class="brand-name" x="62" y="82" font-size="24" fill="var(--card-white)">Lanternfield</text>

      <!-- vertical brand wordmark in clear right margin -->
      <text class="brand-name" transform="translate(912 24) rotate(90)" font-size="54" fill="var(--accent-blue)">Lanternfield</text>

      <!-- identity -->
      <text class="person-name" x="660" y="332" font-size="36" text-anchor="middle" fill="var(--card-white)">Your Name</text>
      <text class="person-title" x="660" y="356" font-size="16" text-anchor="middle" fill="var(--accent-blue)">designation</text>

      <!-- contact panel -->
      <rect class="contact-panel" x="460" y="400" width="400" height="90" fill="var(--contact-panel)"/>
      <text class="contact-line" x="660" y="437" font-size="22" text-anchor="middle" fill="var(--contact-text)">contact@lanternfield.com</text>
      <text class="contact-line" x="660" y="469" font-size="22" text-anchor="middle" fill="var(--contact-text)">lanternfield.com</text>
    </svg>
  </section>
</main>
</body>
</html>
```